Landing Page Design für Speditionsdienstleistungen
Zielgruppe
Express-Transporte / Sonderfahrten / Speditionsdienstleistungen
Aufgabenstellung
- - - WORDPRESS Design gesucht - - -
seriosität für b2b ; primär werden Kastensprinter und Planensprinter eingesetzt , nur Stock Bilder verwenden die ohne ein Abo gekauft werden können ; die präsentation soll das unternehmen gross aussehen lassen, ((bitte die Powerpoint lediglich für die übersicht der dienstleistungen verwenden.)) Es sollte mit dem Firmenlogo harmonieren. Es wird nach einem komplett neuen Design gesucht. Gerne die Farbtöne des Logo verwenden. Es wird nach einer Onepage gesucht mit einem modernen Design für Wordpress.
Ähnlich wie die derzeitige website https://quirlavia-beispiel.de jedoch komplett neu.
Weder mit Website Design noch mit dem der powerpoint bin ich stand jetzt zufrieden.
Ich suche hier nach etwas komplett neuem.
Bereits beantwortete fragen:
1.) Zweck: Vorstellung vom Unternehmen und Dienstleistungen
2.) Zielgruppe: Nekunden / Bestandskunden / generelle übersicht der Dienstleistungen
3.) Auf die Landingpage sollen die im grunde alle Leistungen die wir anbieten und zusätzlich noch einen Text dazu quasi ein über uns Text.
4.) Die Bilder können zur Verfügung gestellt werden. Gerne kann hier jedoch auch via Fotoklarix bsp. 'bessere' Bilder verwendet werden
5.) Gerne darf die Website heller sein ; keine direkte vorstellung der Farben. Ggf. ähnlich dem derzeitgen Logo in die richtung Rot/Grau .. allerdings gerne hier auch freie entscheidung / kreativität
6.) mir gefallen die Website xyz und xyz gut (link bitte anfragen)
Bei fragen bitte melden.
Erreichbar Montag - Freitag 08.00 - 17.00h

```html
<!DOCTYPE html>
<html lang="de">
<head>
<meta charset="utf-8">
<title>Quirlavia – Transport &amp; Spedition</title>
<link href="https://fonts.googleapis.com/css2?family=Montserrat:wght@300;400;500;600;700&display=swap" rel="stylesheet">
<style>
  :root {
    --red: #d42029;
    --red-dark: #b3161d;
    --ink: #2b2b2b;
    --text: #3a3a3a;
    --dark: #333333;
    --darker: #3a3a3a;
    --white: #ffffff;
    --grey: #8a8a8a;
  }
  * { margin: 0; padding: 0; box-sizing: border-box; }
  html, body { width: 1200px; height: 3869px; overflow: hidden; }
  body { position: relative; font-family: "Montserrat", Arial, sans-serif; color: var(--text); background: var(--white); }
  .abs { position: absolute; }

  /* Hero */
  .hero { left: 0; top: 0; width: 1200px; height: 804px;
    background: radial-gradient(ellipse at 78% 25%, #8c7a6c 0%, #5b5550 30%, #3d3d40 60%, #2a2b2f 100%); }
  .logo { left: 90px; top: 20px; color: var(--red); font-weight: 500; font-size: 44px; letter-spacing: 1px; }
  .nav { right: 76px; top: 48px; display: flex; gap: 38px; }
  .nav a { color: var(--white); text-decoration: none; font-weight: 600; font-size: 14px; letter-spacing: .5px; }
  .hero-title { left: 0; width: 1200px; top: 332px; text-align: center; color: var(--red); font-weight: 300; font-size: 74px; letter-spacing: 2px; }
  .hero-sub { left: 0; width: 1200px; top: 408px; text-align: center; color: var(--white); font-weight: 600; font-size: 26px; line-height: 33px; }
  .hero-btn { left: 476px; top: 512px; width: 218px; height: 61px; border: 2px solid var(--white); color: var(--white);
    font-weight: 600; font-size: 20px; display: flex; align-items: center; justify-content: center; }

  /* Photo sections */
  .about-bg { left: 0; top: 804px; width: 1200px; height: 596px;
    background: linear-gradient(90deg, #5d5a55 0%, #77736c 45%, #c9c9c7 75%, #8b8986 100%); }
  .work-bg { left: 0; top: 2040px; width: 1200px; height: 611px;
    background: linear-gradient(90deg, #c74a44 0%, #d9b5a2 28%, #b8b4ae 60%, #7f8288 100%); }

  .card { background: var(--white); padding: 0 40px; }
  .card h2 { color: var(--red); font-weight: 400; font-size: 44px; letter-spacing: 1px; }
  .card p { font-size: 17.5px; line-height: 25.7px; font-weight: 400; color: var(--text); }
  .card p + p { margin-top: 25px; }
  .about-card { left: 95px; top: 870px; width: 694px; height: 480px; padding-top: 28px; }
  .about-card h2 { margin-bottom: 22px; }
  .work-card { left: 430px; top: 2112px; width: 694px; height: 480px; padding-top: 48px; }
  .work-card h2 { margin-bottom: 20px; }
  .work-card p { text-align: justify; }

  /* Services */
  .services { left: 0; top: 1400px; width: 1200px; height: 640px; background: var(--red); }
  .section-title { left: 0; width: 1200px; text-align: center; font-weight: 400; font-size: 45px; line-height: 54px; letter-spacing: 1px; color: var(--white); }
  .service { top: 1601px; width: 321px; height: 322px; background: var(--red-dark); color: var(--white); text-align: center; padding: 22px 36px 0; }
  .service svg { display: block; margin: 0 auto; }
  .service h3 { font-weight: 600; font-size: 18.5px; line-height: 23px; margin: 14px 0 22px; }
  .service p { font-size: 16px; line-height: 19.5px; text-align: justify; text-align-last: center; }
  .dots { display: flex; gap: 12px; }
  .dots span { width: 34px; height: 5px; background: var(--white); }
  .dots span.on { background: var(--ink); }
  .dots.red span.on { background: var(--red); }

  /* Testimonials */
  .reviews { left: 0; top: 2651px; width: 1200px; height: 721px; background: var(--dark); }
  .quote { top: 2874px; width: 330px; }
  .quote svg { position: absolute; left: -44px; top: 0; }
  .quote p { position: absolute; left: 0; top: 36px; width: 265px; color: var(--white); font-size: 17.5px; line-height: 30.4px; text-align: justify; }
  .quote .name { position: absolute; left: 0; top: 346px; color: var(--red); font-weight: 600; font-size: 17.5px; }

  /* Footer */
  .footer h4 { color: var(--red); font-weight: 700; font-size: 22px; letter-spacing: .5px; }
  .links { left: 95px; top: 3542px; font-size: 19.5px; line-height: 30.5px; color: var(--text); }
  .socials { left: 92px; top: 3676px; display: flex; gap: 14px; }
  .socials span { width: 36px; height: 36px; border: 2px solid var(--red); border-radius: 50%; }
  .contact { left: 442px; top: 3547px; font-size: 16.5px; line-height: 30.5px; color: var(--text); }
  .contact .gap { height: 30px; }
  .contact b { color: var(--red); font-weight: 400; }
  .legal { left: 857px; top: 3488px; font-size: 16px; line-height: 19.5px; font-weight: 700; color: var(--ink); }
  .legal b { color: var(--red); }
  .legal .gap { height: 20px; }
  .badge { background: #e6e6e6; border-radius: 4px; }
  .copyright { left: 0; top: 3811px; width: 1200px; height: 58px; background: var(--darker); color: var(--grey);
    font-size: 13.5px; display: flex; align-items: center; justify-content: center; }
</style>
</head>
<body>

<section class="hero abs" role="img" aria-label="Foto: lächelnder Fahrer am Steuer eines Transporters"></section>
<div class="logo abs">QUIRLAVIA</div>
<nav class="nav abs"><a href="#">STARTSEITE</a><a href="#">ÜBER UNS</a><a href="#">LEISTUNGEN</a><a href="#">KONTAKT</a></nav>
<h1 class="hero-title abs">QUIRLAVIA</h1>
<p class="hero-sub abs">Transport | Spedition Zuverlässigkeit und Vertrauen<br>sind unsere Konstante</p>
<a class="hero-btn abs">SEHR GERNE!</a>

<section class="about-bg abs" role="img" aria-label="Foto: weißer Kastensprinter vor einem Gebäude"></section>
<article class="about-card card abs">
  <h2>ÜBER UNS</h2>
  <p>Als gewissenhaftes Inhabergeführtes Unternehmen konzentrieren wir uns auf das machbare.Zuverlässigkeit und Vertrauen sind unsere Konstante. Wir sind stolz darauf, bereits jetzt zurückblickend sagen zu können: „Es hat sich gelohnt!“</p>
  <p>Unsere Zahlen, sowie der gesunde Wachstum sprechen für uns. Wir haben uns innerhalb kürzester Zeit von einem lokalen Spediteur zu einem Europaweit agierenden In-Time Logistikdienstleister entwickelt. Wir sind für alle Herausforderungen offen und lösen auch unmögliche Aufgaben. Hierbei spielt es keine Rolle ob es sich um Einzelaufträge oder Festtouren handelt. Unser Angebot orientiert sich immer an den Bedürfnissen und Erwartungen unser Kunden.Wir versprechen nichts, was wir nicht halten können!</p>
</article>

<section class="services abs"></section>
<h2 class="section-title abs" style="top:1448px">ÜBERSICHT UNSERER<br>DIENSTLEISTUNGEN</h2>

<div class="service abs" style="left:92px">
  <svg width="64" height="64" viewBox="0 0 64 64" fill="none" stroke="#fff" stroke-width="2"><circle cx="32" cy="32" r="29"/><ellipse cx="32" cy="32" rx="13" ry="29"/><line x1="32" y1="3" x2="32" y2="61"/><line x1="3" y1="32" x2="61" y2="32"/><path d="M8 17h48M8 47h48"/></svg>
  <h3>DIREKT- UND<br>EXPRESSTRANSPORTE</h3>
  <p>Wir liefern schnell, flexibel und direkt – das heißt ohne Bei- und Umladung. Ihre zeitkritische Sendung übernehmen wir Bundesweit innerhalb von 60 Minuten.</p>
</div>
<div class="service abs" style="left:446px">
  <svg width="88" height="64" viewBox="0 0 88 64" fill="none" stroke="#fff" stroke-width="2.5"><rect x="4" y="12" width="50" height="34" rx="2"/><path d="M54 22h16l12 14v10H54z"/><circle cx="20" cy="50" r="7" fill="#b3161d"/><circle cx="68" cy="50" r="7" fill="#b3161d"/></svg>
  <h3 style="margin-top:26px;margin-bottom:34px">PROJEKTLOGISTIK</h3>
  <p>Just-in-Time für einen begrenzten Zeitraum? Gerne! Europaweit wickeln wir projektbezogene Transport- und Logistikaufgaben ab.</p>
</div>
<div class="service abs" style="left:805px">
  <svg width="72" height="64" viewBox="0 0 72 64" fill="none" stroke="#fff" stroke-width="2.2"><path d="M22 60s-14-15-14-26a14 14 0 0 1 28 0c0 11-14 26-14 26z"/><circle cx="22" cy="34" r="6"/><path d="M54 34s-10-11-10-19a10 10 0 0 1 20 0c0 8-10 19-10 19z"/><circle cx="54" cy="15" r="4"/><path d="M30 58c10 0 18-6 22-18" stroke-dasharray="3 4"/></svg>
  <h3>REGEL UND<br>FESTTOUREN</h3>
  <p>Sie haben regelmäßig Fahrten zu einem bestimmten Empfänger? Wir übernehmen Ihre Ware zu einem fest vereinbarten Abholtermin und stellen diese je nach Vereinbarung direkt zu.</p>
</div>
<div class="dots abs" style="left:565px;top:1976px"><span class="on"></span><span></span></div>

<section class="work-bg abs" role="img" aria-label="Foto: Fahrerin mit roter Kappe am Steuer eines Transporters"></section>
<article class="work-card card abs">
  <h2>WIE WIR ARBEITEN</h2>
  <p>Wir sind uns darüber bewusst: Zeit ist Geld!<br>Und gerade in dem Bereich der In-Time Logistik gilt diese Redewendung doppelt.</p>
  <p>Im Zentrum unserer Tätigkeit stehen Fahrzeuge mit einer Ladekapazität bis zu 12 Europaletten und einer Zuladung bis 1350 KG. Unser Fokus liegt auf zeitkritischer sowie sensibler Ware.Wir starten direkt nach Beladung, und je Transport übernehmen wir ausschließlich Ihre Ware - so verlieren wir keine wertvolle Zeit und das Risiko einer Beschädigung wird minimiert. Ihnen steht dabei immer das volle Fahrzeug zur Verfügung!Fahrerdaten.</p>
</article>

<section class="reviews abs"></section>
<h2 class="section-title abs" style="top:2719px">WAS UNSERE<br>KUNDEN ÜBER UNS SAGEN</h2>

<div class="quote abs" style="left:137px">
  <svg width="42" height="26" viewBox="0 0 42 26" fill="#d42029"><path d="M0 0h18l-6 26H3zM22 0h18l-6 26h-9z"/></svg>
  <p>Lorem ipsum dolor sit amet, consectetur adipiscing elit, sed do eiusmod tempor incididunt ut labore et dolore magna aliqua. Ut enim ad minim veniam, quis nostrud exercitation ullamco laboris nisi ut aliquip ex ea commodo consequat.</p>
  <div class="name">Tomas Wendler</div>
</div>
<div class="quote abs" style="left:496px">
  <svg width="42" height="26" viewBox="0 0 42 26" fill="#d42029"><path d="M0 0h18l-6 26H3zM22 0h18l-6 26h-9z"/></svg>
  <p>Lorem ipsum dolor sit amet, consectetur adipiscing elit, sed do eiusmod tempor incididunt ut labore et dolore magna aliqua. Ut enim ad minim veniam, quis nostrud exercitation ullamco laboris nisi ut aliquip ex ea commodo consequat.</p>
  <div class="name">Tomas Wendler</div>
</div>
<div class="quote abs" style="left:861px">
  <svg width="42" height="26" viewBox="0 0 42 26" fill="#d42029"><path d="M0 0h18l-6 26H3zM22 0h18l-6 26h-9z"/></svg>
  <p>Lorem ipsum dolor sit amet, consectetur adipiscing elit, sed do eiusmod tempor incididunt ut labore et dolore magna aliqua. Ut enim ad minim veniam, quis nostrud exercitation ullamco laboris nisi ut aliquip ex ea commodo consequat.</p>
  <div class="name">Tomas Wendler</div>
</div>
<div class="dots red abs" style="left:565px;top:3314px"><span class="on"></span><span></span></div>

<footer class="footer">
  <h4 class="abs" style="left:92px;top:3456px">QUICKLINKS</h4>
  <div class="links abs">Startseite<br>AGB<br>Impressum<br>Datenschutz</div>
  <div class="socials abs"><span></span><span></span><span></span></div>

  <h4 class="abs" style="left:442px;top:3456px">KONTAKTINFORMATION</h4>
  <div class="contact abs">
    QUIRLAVIA e.K.<br>Lindenhofweg 14<br>37999 Feldbrunn
    <div class="gap"></div>
    <b>Tel.:</b> +49 (0) 5500 48120 -10<br>
    <b>Fax:</b> +49 (0) 5500 48120 -100<br>
    <b>Mail:</b> kontakt@quirlavia-beispiel.de
  </div>

  <div class="legal abs">
    <b>Registergericht:</b> Feldbrunn<br><b>Registernummer:</b> HRA 400123
    <div class="gap"></div>
    <b>Finanzamt:</b> Feldbrunn<br><b>Umsatzsteuer-ID:</b> DE 100200300
  </div>
  <div class="badge abs" style="left:836px;top:3622px;width:278px;height:48px"></div>
  <div class="badge abs" style="left:854px;top:3688px;width:184px;height:36px"></div>
</footer>

<div class="copyright abs">© 2020 - Copyright QUIRLAVIA e.K - Alle Rechte vorbehalten.</div>

</body>
</html>
```